Tarvex Consulting

Hi,
I have my own network consulting business (just me)
and need to get a logo and business card design together,

Based in New Zealand,

Gareth Holloway
Unified Communications and Network Architect

/design engineer,
and would like this to be the basis for personal branding and company identity

• I have the basis for a optional logo - needs color -

```html
<!DOCTYPE html>
<html lang="en">
<head>
<meta charset="utf-8">
<title>Tarvex Consulting – Business Cards</title>
<link href="https://fonts.googleapis.com/css2?family=Open+Sans:wght@400;600&display=swap" rel="stylesheet">
<style>
  :root {
    --stage: #2b2b2b;
    --card-white: #fdfdfd;
    --ink: #333333;
    --accent: #2a7bbd;
    --white: #ffffff;
    --glow: #6fcde2;
    --cyan: #3fa6d4;
    --blue: #3b6cc0;
    --violet: #3a2e96;
    --mark: #3d8fd0;
  }
  * { margin: 0; padding: 0; box-sizing: border-box; }
  html, body {
    width: 1200px; height: 892px; overflow: hidden;
    background: var(--stage);
    font-family: "Open Sans", Arial, sans-serif;
  }
  .stage { position: relative; width: 1200px; height: 892px; }
  .card {
    position: absolute;
    width: 515px; height: 294px;
    border-radius: 18px;
    overflow: hidden;
  }
  .card--front {
    background: radial-gradient(circle at 42% 58%, var(--glow) 0%, var(--cyan) 30%, var(--blue) 66%, var(--violet) 100%);
  }
  .card--front-a { left: 76px; top: 120px; }
  .card--front-b { left: 605px; top: 120px; }
  .card--back { left: 79px; top: 458px; background: var(--card-white); }

  .front-brand {
    position: absolute; right: 30px; bottom: 16px;
    text-align: right; color: var(--white);
  }
  .brand-name {
    font-weight: 400; letter-spacing: 0.5px;
    text-transform: uppercase; line-height: 1;
  }
  .front-brand .brand-name { font-size: 23px; }
  .front-brand .brand-tagline { font-size: 11.5px; margin-top: 7px; }

  .back-brand { position: absolute; left: 25px; top: 82px; width: 215px; text-align: center; }
  .brand-dot {
    width: 50px; height: 50px; border-radius: 50%;
    background: var(--mark); margin: 0 auto 30px;
  }
  .back-brand .brand-name { font-size: 18px; color: var(--ink); text-align: left; }
  .back-brand .brand-tagline { font-size: 8.6px; color: var(--ink); margin-top: 5px; text-align: left; }

  .contact {
    position: absolute; right: 24px; top: 30px;
    text-align: right; color: var(--ink);
    font-size: 12.5px; line-height: 19px;
  }
  .contact .person { font-size: 17.5px; font-weight: 600; color: var(--accent); line-height: 22px; }
  .contact .role { font-size: 14px; line-height: 20px; }
  .contact .address { margin-top: 62px; }
  .contact .lines { margin-top: 14px; }
  .label, .web-accent { color: var(--accent); }
</style>
</head>
<body>
<main class="stage">
  <section class="card card--front card--front-a">
    <div class="front-brand">
      <p class="brand-name">Tarvex Consulting</p>
      <p class="brand-tagline">Unified Communications and Network Architect</p>
    </div>
  </section>

  <section class="card card--front card--front-b">
    <div class="front-brand">
      <p class="brand-name">Tarvex Consulting</p>
      <p class="brand-tagline">Unified Communications and Network Architect</p>
    </div>
  </section>

  <section class="card card--back">
    <div class="back-brand">
      <div class="brand-dot"></div>
      <p class="brand-name">Tarvex Consulting</p>
      <p class="brand-tagline">Unified Communications and Network Architect</p>
    </div>
    <div class="contact">
      <p class="person">Gareth Holloway</p>
      <p class="role">Design Engineer</p>
      <p class="address">12 Kelvin Lane<br>Wellington 6011<br>Te Aro, New Zealand</p>
      <p class="lines">
        <span class="label">P.</span> 021 555 0148<br>
        <span class="label">M.</span> 021 555 0148<br>
        <span class="label">E.</span> gareth@tarvexconsulting.com<br>
        www.<span class="web-accent">tarvexconsulting</span>.com
      </p>
    </div>
  </section>
</main>
</body>
</html>
```